Coastline Premier Retreats Business Card Design

Design a business card for Coastline Premier Retreats. Look at the website for colors and reference. Card should have logo, name, title, office number, mobile number, email, URL and a tagline like, "Luxury Hotel & Resort Email Marketing" (This might change).

https://www.coastlinepremierretreats.example

The rest I will leave up to your imagination.

Contact Information for Business Card

Logo, name, title, office number, mobile number, email, URL and a tagline like, "Luxury Hotel & Resort Email Marketing" (This might change).

```html
<!DOCTYPE html>
<html lang="en">
<head>
<meta charset="utf-8">
<title>Coastline Premier Retreats – Business Card</title>
<link href="https://fonts.googleapis.com/css2?family=Montserrat:wght@700;800&family=Lato:wght@400;700&family=Dancing+Script:wght@600&display=swap" rel="stylesheet">
<style>
  :root {
    --stage: #2b2b2b;
    --card-dark: #1c1c1d;
    --card-light: #ffffff;
    --accent: #f47b16;
    --ink: #111111;
    --muted: #3c3c3c;
    --silver: #e6e6e6;
    --rule: #cfcfcf;
  }
  * { box-sizing: border-box; margin: 0; padding: 0; }
  html, body {
    width: 1200px; height: 689px; overflow: hidden;
    background: var(--stage);
  }
  .canvas { position: relative; width: 1200px; height: 689px; }

  .card {
    position: absolute;
    width: 525px; height: 300px;
    border-radius: 18px;
    box-shadow: 0 18px 40px rgba(0,0,0,.45);
    overflow: hidden;
  }

  /* Back side */
  .card--back { left: 40px; top: 70px; background: var(--card-dark); }
  .card--back .brand {
    position: absolute; left: 0; right: 0; top: 92px;
    display: flex; align-items: center; justify-content: center; gap: 14px;
  }
  .brand-square { width: 18px; height: 18px; background: var(--accent); flex: none; }
  .brand-name {
    font-family: "Montserrat", sans-serif; font-weight: 800;
    text-transform: uppercase; line-height: 1.1; letter-spacing: .5px;
    white-space: nowrap;
  }
  .card--back .brand-name { color: var(--silver); font-size: 30px; }
  .tagline {
    position: absolute; left: 0; right: 0; top: 200px;
    text-align: center;
    font-family: "Dancing Script", cursive; font-weight: 600;
    font-size: 26px; color: var(--silver);
  }

  /* Front side */
  .card--front { left: 635px; top: 319px; background: var(--card-light); }
  .card--front .brand {
    position: absolute; left: 26px; top: 128px; width: 216px;
    display: flex; align-items: center; gap: 10px;
  }
  .card--front .brand-square { width: 14px; height: 14px; }
  .card--front .brand-name { color: var(--ink); font-size: 13px; letter-spacing: .3px; }
  .divider {
    position: absolute; left: 258px; top: 40px; width: 1px; height: 220px;
    background: linear-gradient(to bottom, transparent, var(--rule) 20%, var(--rule) 80%, transparent);
  }
  .contact { position: absolute; left: 280px; top: 52px; right: 16px; }
  .person-name {
    font-family: "Montserrat", sans-serif; font-weight: 800;
    font-size: 24px; color: var(--ink); letter-spacing: .3px;
  }
  .person-title {
    font-family: "Lato", sans-serif; font-weight: 700;
    font-size: 14px; color: var(--accent); margin-top: 2px;
  }
  .details { list-style: none; margin-top: 16px; }
  .details li {
    display: flex; align-items: flex-start; gap: 8px;
    font-family: "Lato", sans-serif; font-size: 11.5px; line-height: 1.45;
    color: var(--muted); margin-bottom: 4px; white-space: nowrap;
  }
  .details svg { width: 11px; height: 11px; flex: none; margin-top: 3px; fill: var(--accent); }
</style>
</head>
<body>
<main class="canvas">

  <section class="card card--back" aria-label="Card back">
    <div class="brand">
      <span class="brand-square"></span>
      <span class="brand-name">Coastline Premier<br>Retreats</span>
    </div>
    <p class="tagline">Luxury Hotel &amp; Resort Email Marketing</p>
  </section>

  <section class="card card--front" aria-label="Card front">
    <div class="brand">
      <span class="brand-square"></span>
      <span class="brand-name">Coastline Premier<br>Retreats</span>
    </div>
    <div class="divider"></div>
    <div class="contact">
      <h1 class="person-name">DANIEL HARPER</h1>
      <p class="person-title">Founder &amp; CEO</p>
      <ul class="details">
        <li>
          <svg viewBox="0 0 24 24"><path d="M12 2a7 7 0 0 0-7 7c0 5 7 13 7 13s7-8 7-13a7 7 0 0 0-7-7zm0 9.5A2.5 2.5 0 1 1 12 6.5a2.5 2.5 0 0 1 0 5z"/></svg>
          <span>4870 Harbor View Lane<br>Mystic, CT 06355</span>
        </li>
        <li>
          <svg viewBox="0 0 24 24"><path d="M6.6 10.8a15 15 0 0 0 6.6 6.6l2.2-2.2a1 1 0 0 1 1-.25 11.4 11.4 0 0 0 3.6.57 1 1 0 0 1 1 1V20a1 1 0 0 1-1 1A17 17 0 0 1 3 4a1 1 0 0 1 1-1h3.5a1 1 0 0 1 1 1c0 1.25.2 2.450.57 3.57a1 1 0 0 1-.25 1z"/></svg>
          <span>(555) 014-2280</span>
        </li>
        <li>
          <svg viewBox="0 0 24 24"><path d="M7 1h10a2 2 0 0 1 2 2v18a2 2 0 0 1-2 2H7a2 2 0 0 1-2-2V3a2 2 0 0 1 2-2zm0 3v14h10V4zm5 15.5a1 1 0 1 0 0 2 1 1 0 0 0 0-2z"/></svg>
          <span>(555) 014-7391</span>
        </li>
        <li>
          <svg viewBox="0 0 24 24"><path d="M2 5h20v14H2zm2 2v.5l8 5 8-5V7zm0 2.8V17h16V9.8l-8 5z"/></svg>
          <span>info@coastlinepremierretreats.example</span>
        </li>
        <li>
          <svg viewBox="0 0 24 24"><path d="M12 2a10 10 0 1 0 0 20 10 10 0 0 0 0-20zm6.9 6h-3a15 15 0 0 0-1.3-4A8 8 0 0 1 18.9 8zM12 4c.8 1.2 1.5 2.5 1.9 4h-3.8c.4-1.5 1.1-2.8 1.9-4zM4.3 14a8 8 0 0 1 0-4h3.4a16 16 0 0 0 0 4zm.8 2h3a15 15 0 0 0 1.3 4A8 8 0 0 1 5.1 16zm3-8h-3a8 8 0 0 1 4.3-4 15 15 0 0 0-1.3 4zM12 20c-.8-1.2-1.5-2.5-1.9-4h3.8c-.4 1.5-1.1 2.8-1.9 4zm2.3-6H9.7a14 14 0 0 1 0-4h4.6a14 14 0 0 1 0 4zm.3 6a15 15 0 0 0 1.3-4h3a8 8 0 0 1-4.3 4zm1.7-6a16 16 0 0 0 0-4h3.4a8 8 0 0 1 0 4z"/></svg>
          <span>coastlinepremierretreats.example</span>
        </li>
      </ul>
    </div>
  </section>

</main>
</body>
</html>
```